Finiding oppertunites in Real Estate 6.15.20

size of ad 7” x 9.6”
1-I like the ad to stand out and attract people's attention.
2-you should be able to see the text of the ad clearly .. see the attachment anything in yellow is instructions.
3-the list of topics should not be the main part of the ad
4-if you decide you want a picture or vector of a person .. (you decide)
then it should be a white male about 25-30 years old wearing a solid white or blue shirt and not long hair.
5-leave 1 inch for footer
see attachment
Good luck

Target Market(s)

potential male students 25-35 years of age

Industry/Entity Type

Education

Requirements
Must have
• will stand out and people would want to see it.
should be able to read the words of ad
Nice to have
• how to make money in real estate on one line

```html
<!DOCTYPE html>
<html lang="en">
<head>
<meta charset="utf-8">
<title>Real Estate Career Course</title>
<link rel="stylesheet" href="https://fonts.googleapis.com/css2?family=Open+Sans:wght@400;600;700;800&display=swap">
<style>
  :root {
    --ink: #3a3b3d;
    --accent-blue: #0aa3e8;
    --alert-red: #ec4651;
    --rule: #cde6f3;
    --paper: #ffffff;
    --mist: #e3e5e8;
    --border-grey: #6d6f72;
  }
  * { margin: 0; padding: 0; box-sizing: border-box; }
  html, body { width: 743px; height: 1200px; overflow: hidden; background: var(--paper); }
  .flyer {
    position: relative; width: 743px; height: 1200px; overflow: hidden;
    background: var(--paper);
    font-family: "Open Sans", Arial, sans-serif; color: var(--ink);
  }
  .corner-texture {
    position: absolute; top: 0; right: 0; width: 420px; height: 720px;
    background: radial-gradient(ellipse at 85% 10%, var(--mist) 0%, rgba(227,229,232,0.55) 35%, rgba(255,255,255,0) 70%);
  }
  .line {
    position: absolute; left: 0; width: 100%; text-align: center;
    font-weight: 700; white-space: nowrap; line-height: 1;
    transform: translateY(-50%);
  }
  .highlight { color: var(--accent-blue); }
  .title { top: 114px; font-size: 38px; }
  .hook { font-size: 30px; }
  .statement { font-size: 31px; }
  .rule {
    position: absolute; left: 115px; width: 515px; height: 1px;
    background: linear-gradient(90deg, rgba(205,230,243,0), var(--rule) 20%, var(--rule) 80%, rgba(205,230,243,0));
  }
  .remote-pill {
    position: absolute; left: 269px; top: 489px; width: 197px; height: 42px;
    border-radius: 10px; background: var(--alert-red);
    box-shadow: 0 2px 4px rgba(0,0,0,0.15);
    color: #fff; font-weight: 700; font-size: 20px;
    display: flex; align-items: center; justify-content: center;
  }
  .session-count { top: 575px; font-size: 31px; }
  .start-date {
    position: absolute; left: 164px; top: 617px; width: 406px; height: 66px;
    border: 1.5px solid var(--border-grey); border-radius: 9px; overflow: hidden;
    display: flex; font-weight: 700; font-size: 31px;
  }
  .start-date .label { flex: 0 0 265px; display: flex; align-items: center; justify-content: center; }
  .start-date .date { flex: 1; background: var(--accent-blue); color: #fff; display: flex; align-items: center; justify-content: center; }
  .students-photo {
    position: absolute; left: 242px; top: 697px; width: 281px; height: 285px;
    background: radial-gradient(ellipse at 50% 55%, #8fa3bd 0%, #b9c6d6 45%, rgba(255,255,255,0) 75%);
  }
  .topics-heading { top: 1007px; font-size: 23px; font-weight: 600; color: var(--accent-blue); }
  .topics-dash { position: absolute; left: 352px; top: 1031px; width: 39px; height: 3px; background: #555; }
  .topics-list {
    position: absolute; left: 0; top: 1049px; width: 100%;
    text-align: center; font-size: 12.5px; font-weight: 400; line-height: 19px; color: #444;
  }
</style>
</head>
<body>
<main class="flyer">
  <div class="corner-texture" role="img" aria-label="Soft grey dotted diamond texture in the upper right"></div>

  <h1 class="line title">Real Estate Career Course</h1>
  <div class="rule" style="top:150px"></div>

  <p class="line hook" style="top:176px">How to <span class="highlight">Make Money</span></p>
  <p class="line hook" style="top:217px">in Real Estate?</p>
  <div class="rule" style="top:245px"></div>

  <p class="line statement" style="top:279px">For those who have started or</p>
  <p class="line statement" style="top:321px">would like to go into <span class="highlight">Real Estate</span></p>
  <div class="rule" style="top:361px"></div>

  <p class="line statement" style="top:389px">An investment in knowledge</p>
  <p class="line statement" style="top:437px">opens up untold <span class="highlight">opportunities</span></p>

  <div class="remote-pill">Remote sessions</div>

  <p class="line session-count">12 session course</p>

  <div class="start-date">
    <span class="label">Classes starting</span>
    <span class="date">June 16</span>
  </div>

  <div class="students-photo" role="img" aria-label="Photo of a smiling young man holding a small model house, with a group of students standing behind him"></div>

  <h2 class="line topics-heading">A partial listing of Topics</h2>
  <div class="topics-dash"></div>
  <p class="topics-list">
    Single-family | Multifamily | Management | Real Estate Concepts | Real Estate law | Investment<br>
    properties | Foreclosures Rehab | &nbsp;Foreclosures | Short sales | Development | Finical modeling<br>
    HUD properties | Due Diligence e
  </p>
</main>
</body>
</html>
```